UX Design for Analytics Web Application

http://velqoranthe.com/
We are tech & consulting company with analytics products (web applications), located at Rio de Janeiro, Brazil.

We are searching a partner do develop UX for our products, i.e, aesthetics, usability, HTML/CSS.

Currently we have a product suite and the goal is to make a pilot re-design project with one of our products.

The product of interest is interactive webapp that aims at data analysis, significantly different from blogs, e-commerce or landing pages.

We do have a software development team but we lack an UX & HTML expert. Currently we use Bootstrap templates but the results are insatisfatory.

So, the project scope is, to develop the arts (UX, aesthetics, etc) along with the code/mockup (HTML/CSS) for one of our product (3 pages).

This is a pilot project and there's potential to rehire for our other products. Code quality is of importance.

More details and specification can be found in attached files.

Target Market(s)

Executives, managers & consultants

Industry/Entity Type

It Company

Coding

Coded - Design and coding required

Number of Pages Required

3 page

Font styles to use
Sans Serif

Requirements
Must have
• (see attached files, prefer the pptx version))
• -Responsive
Nice to have
• (see attached files, prefer the pptx version)
Should not have
• -Avoid Green, Red and Yellow colors. They have a meaning of good, bad and average in our products.

```html
<!DOCTYPE html>
<html lang="en">
<head>
<meta charset="utf-8">
<title>Velqoranthe – Process Overview</title>
<link href="https://fonts.googleapis.com/css2?family=Montserrat:wght@400;500;600&display=swap" rel="stylesheet">
<style>
  :root {
    --accent: #1f4e79;
    --accent-soft: #3a6ea5;
    --text: #444444;
    --text-strong: #3a3a3a;
    --panel: #f7f7f7;
    --border: #cccccc;
    --header-line: #e6e6e6;
    --pager-line: #e2e2e2;
    --muted: #bdbdbd;
    --white: #ffffff;
  }
  * { box-sizing: border-box; margin: 0; padding: 0; }
  html, body { width: 1124px; height: 1200px; overflow: hidden; }
  body {
    position: relative;
    background: var(--white);
    font-family: "Montserrat", sans-serif;
    color: var(--text);
  }
  .site-header {
    position: absolute; left: 0; top: 0; width: 1124px; height: 74px;
    border-bottom: 1px solid var(--header-line);
    box-shadow: 0 1px 3px rgba(0,0,0,0.05);
  }
  .brand {
    position: absolute; left: 92px; top: 20px;
    display: flex; align-items: center; gap: 10px;
    font-size: 28px; font-weight: 600; color: var(--text-strong);
    text-decoration: none;
  }
  .brand-dot {
    width: 32px; height: 32px; border-radius: 50%;
    border: 3px solid var(--text-strong);
  }
  .header-icons { position: absolute; top: 29px; left: 920px; display: flex; gap: 28px; }
  .header-icons svg { width: 18px; height: 18px; fill: var(--accent); }

  .overview {
    position: absolute; left: 82px; top: 120px; width: 960px; height: 300px;
    background: var(--panel); border: 1px solid var(--border);
  }
  .overview-art {
    position: absolute; left: 70px; top: 41px; width: 201px; height: 240px;
    border-radius: 100px 100px 20px 20px;
    background: radial-gradient(circle at 45% 40%, #e8e8e8 0%, #eeeeee 60%, #f3f3f3 100%);
  }
  .overview-title {
    position: absolute; left: 380px; top: 42px;
    font-size: 21px; font-weight: 500; letter-spacing: 0.5px; color: var(--text-strong);
  }
  .overview-list { position: absolute; left: 383px; top: 88px; width: 560px; }
  .overview-row { display: flex; height: 32px; align-items: center; font-size: 16px; font-weight: 500; }
  .overview-row dt { width: 327px; }
  .overview-row dd { display: flex; gap: 24px; }

  .process-grid {
    position: absolute; left: 87px; top: 456px;
    display: grid; grid-template-columns: repeat(3, 303px);
    column-gap: 22px; row-gap: 30px;
  }
  .process-card {
    height: 185px; background: var(--panel);
    border: 1px solid var(--border); border-radius: 5px;
    padding: 29px 0 0 28px;
  }
  .process-card h2 { font-size: 21px; font-weight: 500; color: var(--text-strong); margin-bottom: 8px; line-height: 26px; }
  .process-card p { font-size: 13.5px; font-weight: 500; line-height: 32px; white-space: nowrap; }
  .process-card p span + span { margin-left: 15px; }

  .btn-create {
    position: absolute; left: 87px; top: 1098px; width: 203px; height: 43px;
    background: var(--accent-soft); color: var(--white); border-radius: 4px;
    display: flex; align-items: center; justify-content: center; gap: 8px;
    font-family: inherit; font-size: 16px; font-weight: 500; border: none;
  }
  .btn-create svg { width: 14px; height: 14px; }

  .pagination {
    position: absolute; left: 744px; top: 1107px; height: 21px;
    display: flex; border: 1px solid var(--pager-line); font-size: 9px;
  }
  .pagination a {
    display: flex; align-items: center; justify-content: center;
    text-decoration: none; color: var(--accent); font-weight: 600;
    border-right: 1px solid var(--pager-line); width: 22px; font-size: 11px;
  }
  .pagination a:last-child { border-right: none; }
  .pagination .page-prev { width: 93px; color: var(--muted); font-size: 8px; font-weight: 400; }
  .pagination .page-next { width: 94px; font-size: 9px; font-weight: 500; }
  .pagination .is-current { background: var(--accent); color: var(--white); }
  .pagination .page-gap { color: var(--muted); }

  .site-footer {
    position: absolute; left: 0; top: 1158px; width: 1124px; height: 42px;
    background: var(--accent); color: var(--white);
    display: flex; align-items: center; justify-content: center;
    font-size: 11px; font-weight: 500;
  }
  .footer-code { position: absolute; right: 20px; top: 14px; font-size: 10px; }
</style>
</head>
<body>
  <header class="site-header">
    <a class="brand" href="http://velqoranthe.com/"><span class="brand-dot"></span>Velqoranthe</a>
    <nav class="header-icons">
      <svg viewBox="0 0 20 20" aria-label="Info"><circle cx="10" cy="10" r="10"/><rect x="8.5" y="8" width="3" height="8" fill="#fff"/><circle cx="10" cy="5" r="1.7" fill="#fff"/></svg>
      <svg viewBox="0 0 20 20" aria-label="Account"><circle cx="10" cy="5.5" r="4.5"/><path d="M2 20v-3c0-4 3-6 8-6s8 2 8 6v3z"/></svg>
      <svg viewBox="0 0 20 20" aria-label="Menu"><rect x="0" y="3" width="20" height="2.4"/><rect x="7" y="7.2" width="13" height="2.4"/><rect x="7" y="11.4" width="13" height="2.4"/><rect x="0" y="15.6" width="20" height="2.4"/><path d="M5 7v6.8L1 10.4z"/></svg>
    </nav>
  </header>

  <section class="overview">
    <div class="overview-art" role="img" aria-label="Illustration of a head in profile with gears"></div>
    <h1 class="overview-title">PROCESS OVERVIEW</h1>
    <dl class="overview-list">
      <div class="overview-row"><dt>Number of active processes</dt><dd>25</dd></div>
      <div class="overview-row"><dt>Number of completed processes</dt><dd>50</dd></div>
      <div class="overview-row"><dt>Completion</dt><dd>72%</dd></div>
      <div class="overview-row"><dt>Activity feed</dt><dd>Loreum Ipsum</dd></div>
      <div class="overview-row"><dt></dt><dd><span>Lena Markov</span><span>30/3/2017</span></dd></div>
      <div class="overview-row"><dt>Expenses ($) of all processes</dt><dd>$5865</dd></div>
    </dl>
  </section>

  <main class="process-grid">
    <article class="process-card"><h2>Process #1</h2><p><span>Expenses ($) process cost</span><span>$256</span></p><p><span>Status descriptlion</span><span>Loreum Ipsum</span></p><p><span>Current stage</span><span>Executive Negatiation</span></p></article>
    <article class="process-card"><h2>Process #2</h2><p><span>Expenses ($) process cost</span><span>$256</span></p><p><span>Status descriptlion</span><span>Loreum Ipsum</span></p><p><span>Current stage</span><span>Executive Negatiation</span></p></article>
    <article class="process-card"><h2>Process #3</h2><p><span>Expenses ($) process cost</span><span>$256</span></p><p><span>Status descriptlion</span><span>Loreum Ipsum</span></p><p><span>Current stage</span><span>Executive Negatiation</span></p></article>
    <article class="process-card"><h2>Process #4</h2><p><span>Expenses ($) process cost</span><span>$256</span></p><p><span>Status descriptlion</span><span>Loreum Ipsum</span></p><p><span>Current stage</span><span>Executive Negatiation</span></p></article>
    <article class="process-card"><h2>Process #5</h2><p><span>Expenses ($) process cost</span><span>$256</span></p><p><span>Status descriptlion</span><span>Loreum Ipsum</span></p><p><span>Current stage</span><span>Executive Negatiation</span></p></article>
    <article class="process-card"><h2>Process #6</h2><p><span>Expenses ($) process cost</span><span>$256</span></p><p><span>Status descriptlion</span><span>Loreum Ipsum</span></p><p><span>Current stage</span><span>Executive Negatiation</span></p></article>
    <article class="process-card"><h2>Process #7</h2><p><span>Expenses ($) process cost</span><span>$256</span></p><p><span>Status descriptlion</span><span>Loreum Ipsum</span></p><p><span>Current stage</span><span>Executive Negatiation</span></p></article>
    <article class="process-card"><h2>Process #8</h2><p><span>Expenses ($) process cost</span><span>$256</span></p><p><span>Status descriptlion</span><span>Loreum Ipsum</span></p><p><span>Current stage</span><span>Executive Negatiation</span></p></article>
    <article class="process-card"><h2>Process #9</h2><p><span>Expenses ($) process cost</span><span>$256</span></p><p><span>Status descriptlion</span><span>Loreum Ipsum</span></p><p><span>Current stage</span><span>Executive Negatiation</span></p></article>
  </main>

  <button class="btn-create" type="button">
    <svg viewBox="0 0 14 14"><circle cx="7" cy="7" r="7" fill="#fff"/><rect x="6" y="3" width="2" height="8" fill="#3a6ea5"/><rect x="3" y="6" width="8" height="2" fill="#3a6ea5"/></svg>
    Create New Process
  </button>

  <nav class="pagination">
    <a class="page-prev" href="#">Previous Page</a>
    <a class="is-current" href="#">1</a>
    <a href="#">2</a>
    <a href="#">3</a>
    <a href="#">4</a>
    <a class="page-gap" href="#">…</a>
    <a class="page-next" href="#">Next Page</a>
  </nav>

  <footer class="site-footer">
    © Velqoranthe Partners2017. All Rights Reserved.
    <span class="footer-code">C12</span>
  </footer>
</body>
</html>
```